Silvermoor Property Development Co.

We need a logo and business card design for a Hong Kong based real estate company, PLX Land. We are want the brand to reflect the owners forward thinking, creative, and trend setting projects, while also reflecting a sense of security and strength. We invest in industrial properties which we convert to co-living or co-working spaces. PLX stands for Greater Bay Area which is the region around southern China including HK, Macau, and 9 other Chinese cities...made up of approx. 68 million people. There are massive infrastructure projects including the bridge to Macau and high-speed rail to SZ and the bridge connecting SZ and Zhongshan.

Target Market(s)

Chinese and western retail investors, as well as institutional investors

Industry/Entity Type

Real Estate Development

Contact Information for Business Card

Dale Whitford
CEO
dale@plxland-example.com
M + 852 9581 4062
F + 852 3864 2217
Suite 2207, The Halvern, 41 Tremont Rd., Central, Hong Kong

Logo Text

plx land (company name) lifestyle property development (underneath)

Colors

Designer to choose colors to be used in the design.

Requirements
Must have
• Details listed above. One side should include the logo and company name...plx land in modern, hip styling with "lifestyle property development"
Nice to have
• Could be a Black card, with metallic purple "plx" and white "land"...but open great design ideas
Should not have
• boring and traditional layout

```html
<!DOCTYPE html>
<html lang="en">
<head>
<meta charset="utf-8">
<title>PLX Land – Business Card</title>
<link rel="stylesheet" href="https://fonts.googleapis.com/css2?family=Bebas+Neue&family=Open+Sans:wght@400&display=swap">
<style>
  :root {
    --backdrop: #2a2a2b;
    --card: #1d1d1f;
    --card-edge: #262628;
    --purple: #9a22b4;
    --white: #f2f2f2;
    --silver: #cfcfd2;
    --muted: #bdbdc0;
    --rule: #4a4a4e;
    --pattern-a: #232326;
    --pattern-b: #29292c;
  }
  * { margin: 0; padding: 0; box-sizing: border-box; }
  html, body { width: 1200px; height: 1108px; overflow: hidden; }
  body {
    background: var(--backdrop);
    font-family: "Open Sans", Arial, sans-serif;
    position: relative;
  }
  .card {
    position: absolute;
    top: 224px;
    width: 420px;
    height: 660px;
    border-radius: 24px;
    background: var(--card);
    box-shadow: 0 18px 40px rgba(0,0,0,.45);
    overflow: hidden;
  }
  .card--front { left: 150px; }
  .card--back { left: 630px; }

  /* Front */
  .brand-name {
    font-family: "Bebas Neue", Impact, sans-serif;
    font-weight: 400;
    color: var(--purple);
    letter-spacing: 1px;
    line-height: 1;
  }
  .card--front .brand-name {
    position: absolute;
    top: 120px;
    left: 0; right: 0;
    text-align: center;
    font-size: 96px;
  }
  .contact {
    position: absolute;
    top: 340px;
    left: 0; right: 0;
    text-align: center;
  }
  .contact__name {
    font-family: "Bebas Neue", Impact, sans-serif;
    color: var(--purple);
    font-size: 34px;
    line-height: 1;
  }
  .contact__role {
    color: var(--muted);
    font-size: 15px;
    margin-top: 2px;
  }
  .rule {
    width: 160px;
    height: 1px;
    background: var(--rule);
    margin: 12px auto;
  }
  .contact__lines {
    list-style: none;
    color: var(--white);
    font-size: 16px;
    line-height: 1.45;
  }
  .contact__label { color: var(--purple); margin-right: 4px; }
  .contact__address {
    color: var(--white);
    font-size: 16px;
    line-height: 1.45;
    font-style: normal;
  }

  /* Back */
  .back-pattern {
    position: absolute;
    inset: 0;
    background: linear-gradient(160deg, var(--pattern-b), var(--pattern-a) 70%);
  }
  .back-brand {
    position: absolute;
    left: 0; right: 0;
    bottom: 90px;
    text-align: center;
  }
  .card--back .brand-name {
    color: var(--silver);
    font-size: 104px;
  }
  .tagline {
    font-family: "Bebas Neue", Impact, sans-serif;
    color: var(--silver);
    font-size: 24px;
    letter-spacing: 2px;
    margin-top: 10px;
  }
</style>
</head>
<body>
  <article class="card card--front" aria-label="Business card front">
    <div class="brand-name">PLX Land</div>
    <section class="contact">
      <h1 class="contact__name">Dale Whitford</h1>
      <p class="contact__role">CEO</p>
      <div class="rule"></div>
      <ul class="contact__lines">
        <li><span class="contact__label">M:</span>+ 852 9581 4062</li>
        <li><span class="contact__label">F:</span>+ 852 3864 2217</li>
        <li><span class="contact__label">E:</span>dale@plxland-example.com</li>
      </ul>
      <div class="rule"></div>
      <address class="contact__address">
        Suite 2207, The Halvern<br>
        41 Tremont Rd., Central, Hong Kong
      </address>
    </section>
  </article>

  <article class="card card--back" aria-label="Business card back">
    <div class="back-pattern" role="img" aria-label="Faint repeating brand-name pattern across the card background"></div>
    <div class="back-brand">
      <div class="brand-name">PLX Land</div>
      <p class="tagline">Lifestyle Property Development</p>
    </div>
  </article>
</body>
</html>
```